New business card/stationary for a consulting company

I am looking for a clean and very professional looking business card for my consulting company as well as corresponding stationary. I am uploading our logo. I like simple and powerful for the feel. No graphics but I am open on everything else. Below is my contact information but would like the final to be in a version I can add my employees information into and print. Thank you.

Daniel Whitcombe
dan@ferncliffadvisory.com
2870 North 9th Avenue, Summit Floor, Elm Ridge, Illinois 60531
www.ferncliffadvisory.com

Industry/Entity Type

Consulting

Contact Information for Business Card

Daniel Whitcombe
dan@ferncliffadvisory.com
www.ferncliffadvisory.com

Font styles to use
Serif
Sans Serif

Requirements
Must have
• Our logo and the business card details.
Nice to have
• our website www.ferncliffadvisory.com

```html
<!DOCTYPE html>
<html lang="en">
<head>
<meta charset="UTF-8">
<title>Ferncliff Advisory — Business Card</title>
<link rel="stylesheet" href="https://fonts.googleapis.com/css2?family=Open+Sans:wght@400;600;700&display=swap">
<style>
  :root {
    --backdrop: #2a2a2c;
    --navy: #13127a;
    --royal: #3b2fd9;
    --deep: #07075c;
    --ink: #1c1a7e;
    --text-grey: #55565c;
    --paper: #fbfbfb;
    --rule: #c9c9cf;
    --white: #ffffff;
  }
  * { box-sizing: border-box; margin: 0; padding: 0; }
  html, body {
    width: 1200px; height: 900px; overflow: hidden;
    background: var(--backdrop);
    font-family: "Open Sans", Arial, sans-serif;
  }
  .canvas {
    width: 1200px; height: 900px;
    display: flex; flex-direction: column; align-items: center; justify-content: center;
    gap: 40px;
  }
  .card {
    width: 700px; height: 400px; position: relative; overflow: hidden;
    box-shadow: 0 14px 30px rgba(0,0,0,0.45);
  }

  /* Back of card */
  .card-back {
    background: linear-gradient(100deg, var(--royal) 0%, #1f19a8 45%, var(--deep) 100%);
    color: var(--white);
    display: flex; flex-direction: column; align-items: center; justify-content: center;
  }
  .brand { display: flex; align-items: center; gap: 14px; }
  .brand-square { width: 26px; height: 26px; flex: none; }
  .card-back .brand-square { background: var(--white); }
  .brand-name {
    font-weight: 400; font-size: 34px; letter-spacing: 1px; text-transform: uppercase;
    line-height: 1;
  }
  .back-web {
    margin-top: 70px; font-size: 15px; letter-spacing: 6px;
  }

  /* Front of card */
  .card-front { background: var(--paper); }
  .front-band {
    position: absolute; left: 0; right: 0; bottom: 0; height: 16px;
    background: linear-gradient(90deg, var(--royal), var(--navy));
  }
  .front-brand {
    position: absolute; left: 60px; top: 120px; color: var(--ink);
  }
  .front-brand .brand-square { background: var(--ink); }
  .front-brand .brand-name { font-size: 28px; }
  .person-name {
    position: absolute; left: 60px; top: 250px;
    font-weight: 700; font-size: 20px; color: var(--ink);
    letter-spacing: 0.3px; text-transform: uppercase;
  }
  .divider {
    position: absolute; left: 395px; top: 110px; width: 1px; height: 190px;
    background: linear-gradient(var(--paper), var(--rule) 30%, var(--rule) 70%, var(--paper));
  }
  .contact {
    position: absolute; left: 420px; top: 118px;
    font-size: 14.5px; line-height: 1.45; color: var(--text-grey);
  }
  .address { margin-bottom: 6px; }
  .contact-row { display: flex; align-items: center; gap: 8px; }
  .contact-row svg { width: 13px; height: 13px; flex: none; }
</style>
</head>
<body>
<main class="canvas">
  <section class="card card-back">
    <div class="brand">
      <span class="brand-square"></span>
      <span class="brand-name">Ferncliff Advisory</span>
    </div>
    <p class="back-web">www.ferncliffadvisory.com</p>
  </section>

  <section class="card card-front">
    <div class="brand front-brand">
      <span class="brand-square"></span>
      <span class="brand-name">Ferncliff Advisory</span>
    </div>
    <p class="person-name">Daniel Whitcombe</p>
    <div class="divider"></div>
    <div class="contact">
      <p class="address">2870 North 9th Avenue<br>Summit Floor, Elm Ridge<br>Illinois 60531</p>
      <p class="contact-row">
        <svg viewBox="0 0 16 16" aria-hidden="true"><rect x="1" y="3" width="14" height="10" rx="1" fill="#55565c"/><path d="M1.5 3.5 8 9l6.5-5.5" fill="none" stroke="#fbfbfb" stroke-width="1.4"/></svg>
        dan@ferncliffadvisory.com
      </p>
      <p class="contact-row">
        <svg viewBox="0 0 16 16" aria-hidden="true"><circle cx="8" cy="8" r="7" fill="#55565c"/><path d="M1 8h14M8 1c-3 3-3 11 0 14M8 1c3 3 3 11 0 14" fill="none" stroke="#fbfbfb" stroke-width="1.1"/></svg>
        www.ferncliffadvisory.com
      </p>
    </div>
    <div class="front-band"></div>
  </section>
</main>
</body>
</html>
```